Business Card for Fashion House

We need a business card design for our personalize fashion service for our customers. the business card should reflect reliability, luxury and creativity.
The brand Gravetto is extracted from "Graceful Velvetto"; Gravetto provides fashion designs sprinkled with luxury and style tailored for our elite clients character profile.
Gravetto is created for those who embody class and elegance with a passion for style.
Target Market(s)
Affluent Customers
Industry/Entity Type
Fashion
Contact Information for Business Card
Samira Haddadin
Fashion Designer
Telephone: +971 4 555 0192
Mobile +971 50 555 0147
Emal info@gravetto-example.com
Website www.gravetto-example.com
Social Media Youtube g+ Facebook Instagram Pin /gravetto
Font styles to use
Other font styles liked:
- Audrey provided
Look and feel
Each slider illustrates characteristics of the customer's brand and the style your logo design should communicate.

```html
<!DOCTYPE html>
<html lang="en">
<head>
<meta charset="utf-8">
<title>Gravetto Business Card</title>
<link href="https://fonts.googleapis.com/css2?family=Marcellus&family=Roboto:wght@400&display=swap" rel="stylesheet">
<style>
  :root {
    --backdrop: #4b4b4d;
    --card: #1d1d1f;
    --silver: #d9d9dc;
    --white: #f4f4f4;
    --muted: #a9a9ad;
  }
  * { margin: 0; padding: 0; box-sizing: border-box; }
  html, body { width: 799px; height: 1200px; overflow: hidden; }
  body {
    background: var(--backdrop);
    font-family: "Roboto", Arial, sans-serif;
    position: relative;
  }
  .card {
    position: absolute;
    left: 100px;
    width: 600px;
    height: 343px;
    background: var(--card);
    box-shadow: 0 10px 30px rgba(0,0,0,0.45);
  }
  .card--front { top: 140px; }
  .card--back { top: 718px; }

  .brand {
    position: absolute;
    left: 0; right: 0;
    top: 92px;
    display: flex;
    flex-direction: column;
    align-items: center;
    gap: 26px;
  }
  .brand__dot {
    width: 74px; height: 74px;
    border: 3px solid var(--silver);
    border-radius: 50%;
  }
  .brand__name {
    font-family: "Marcellus", Georgia, serif;
    font-size: 34px;
    letter-spacing: 16px;
    padding-left: 16px;
    color: var(--silver);
  }

  .person { position: absolute; left: 34px; top: 30px; }
  .person__name {
    font-family: "Marcellus", Georgia, serif;
    font-size: 20px;
    color: var(--white);
  }
  .person__title { font-size: 9px; color: var(--muted); margin-top: 2px; }

  .contacts {
    position: absolute;
    left: 34px; bottom: 70px;
    list-style: none;
    display: flex;
    flex-direction: column;
    gap: 3px;
  }
  .contacts li {
    display: flex; align-items: center; gap: 12px;
    font-size: 13px; color: var(--white);
  }
  .contacts svg { width: 12px; height: 12px; flex: none; }

  .back-mark {
    position: absolute;
    right: 50px; top: 108px;
    display: flex; align-items: center; gap: 14px;
  }
  .back-mark__dot {
    width: 96px; height: 96px;
    border: 6px solid var(--white);
    border-radius: 50%;
  }

  .social {
    position: absolute;
    right: 40px; bottom: 30px;
    display: flex; align-items: center; gap: 8px;
    font-size: 15px; color: var(--white);
  }
  .social__dot { width: 12px; height: 12px; border-radius: 50%; background: var(--white); }
</style>
</head>
<body>
  <section class="card card--front">
    <div class="brand">
      <span class="brand__dot"></span>
      <span class="brand__name">GRAVETTO</span>
    </div>
  </section>

  <section class="card card--back">
    <div class="person">
      <p class="person__name">Samira Haddadin</p>
      <p class="person__title">Fashion Designer</p>
    </div>

    <ul class="contacts">
      <li>
        <svg viewBox="0 0 12 12" fill="none" stroke="#f4f4f4" stroke-width="1.2"><path d="M3 1.5l1.5 2.5-1 1c.6 1.4 1.6 2.4 3 3l1-1 2.5 1.5-.8 1.8C5.5 10 2 6.5 1.7 2.3z"/></svg>
        +971 4 555 0192
      </li>
      <li>
        <svg viewBox="0 0 12 12" fill="none" stroke="#f4f4f4" stroke-width="1.2"><rect x="3" y="1" width="6" height="10" rx="1"/><line x1="5" y1="9" x2="7" y2="9"/></svg>
        +971 50 555 0147
      </li>
      <li>
        <svg viewBox="0 0 12 12" fill="none" stroke="#f4f4f4" stroke-width="1.2"><rect x="1" y="2.5" width="10" height="7"/><path d="M1 2.5l5 4 5-4"/></svg>
        info@gravetto-example.com
      </li>
      <li>
        <svg viewBox="0 0 12 12" fill="none" stroke="#f4f4f4" stroke-width="1.1"><circle cx="6" cy="6" r="5"/><ellipse cx="6" cy="6" rx="2.2" ry="5"/><line x1="1" y1="6" x2="11" y2="6"/></svg>
        www.gravetto-example.com
      </li>
    </ul>

    <div class="back-mark">
      <span class="back-mark__dot"></span>
    </div>

    <div class="social">
      <span class="social__dot"></span>
      <span>/gravetto</span>
    </div>
  </section>
</body>
</html>
```